PostCard Design Project

I am making a mailing postcard
I am having the mailing printed using 4 color foil on certain parts.
I am looking for a design that maximizes the foil process where certain parts are done in foil to grab the customers attention (example: if there is a car on the postcard the headlights would be done in foil) .
I am targeting some industries, (auto, real estate, medical, beauty) I would like the post card to have examples of postcard ideas for 2 or 3 of these industries.
specs:
the postcard should be atleast 6.5x9 up to 8.5x11, I don't want to restrict the space for the creative as I don't want everything to look like a huge mess. both sides will be used.
the piece is a direct mail piece so it has to meet requirements of https://www.mailvantor.com/business/pdf/quick-reference-guide.pdf
text will be
"business with no limits, meet mailing with no addresses, gain new customers through "Open Porch Route Drop" reach new customers at their home without needing their address. "
I also want some current print specials I am running included.
-double your order FREE (order 500 business cards and get 1000)
-250 100lb gloss stock brochures 99.00
-business packages (cards, envelopes and letterhead) 299
-1000 flyers 140.40
-5000 postcards 179.99
A list of services
banners
booklets
brochures
business cards
calendars
catalogs
CD/DVD packages
envelopes
event tickets
flyers
hangtags
postcards
posters
presentation folders
rack cards
labels
table tents
window cling and decal
"order 24/7 orders@inkwillow.com" must be included
my logo is InkWillow will be supplied later
ive received some great designs. however Im looking for something a little more modern like some zorvel would put out. if the amount of words is too much please feel free to edit. also an idea i had for the list of services i offer is to have it transparent yet readable as the background of the postcard some small some big but covering the entire backgroud. you can then design on top of that with other thing. just an early morning thought
Reason: I have uploaded a sketch of my idea, please take time to look at it for an accurate depiction of what im looking for. feel free to add elements that make it pop off the page
Reason: We are getting close i will be providing feed back today

```html
<!DOCTYPE html>
<html lang="en">
<head>
<meta charset="utf-8">
<title>InkWillow Mailer Postcard – Front and Back</title>
<link rel="stylesheet" href="https://fonts.googleapis.com/css2?family=PT+Sans:ital,wght@0,400;0,700;1,400;1,700&family=Zilla+Slab:wght@300;400;500;600&display=swap">
<style>
  :root {
    --page: #ffffff;
    --ink-black: #000000;
    --ink-white: #ffffff;
    --auto-blue: #1f7fc4;
    --auto-grey: #5a5a5a;
    --lorem-grey: #8a8a8a;
    --estate-green: #8cc63f;
    --estate-yellow: #e8f08a;
    --dental-blue: #1a7fc9;
    --body-ink: #222222;
    --rule: #6f6f6f;
    --logo-grey: #b0b0b0;
    --slab: "Zilla Slab", Georgia, serif;
    --sans: "PT Sans", Arial, sans-serif;
  }
  * { box-sizing: border-box; margin: 0; padding: 0; }
  html, body { width: 1200px; height: 420px; overflow: hidden; background: var(--page); }
  .canvas { position: relative; width: 1200px; height: 420px; background: var(--page); }

  .postcard {
    position: absolute; top: 12px; width: 539px; height: 391px; overflow: hidden;
    box-shadow: 4px 5px 6px rgba(0,0,0,.35);
  }
  .postcard--front { left: 44px; background: var(--ink-black); }
  .postcard--back { left: 625px; background: var(--ink-white); }

  /* Front */
  .front__glow {
    position: absolute; left: 292px; top: -18px; width: 320px; height: 320px;
    background: radial-gradient(circle at 50% 50%, rgba(255,255,255,.95) 0%, rgba(255,255,255,.55) 8%, rgba(140,140,140,.3) 30%, rgba(0,0,0,0) 62%);
  }
  .front__headline {
    position: absolute; left: 21px; top: 19px;
    font-family: var(--slab); font-weight: 300; font-size: 41px; line-height: 47px;
    color: var(--ink-white); letter-spacing: 1.3px; text-transform: uppercase;
  }
  .front__order {
    position: absolute; left: 21px; top: 116px;
    font-family: var(--slab); font-weight: 600; font-size: 20px; color: var(--ink-white);
  }

  .sample { position: absolute; overflow: hidden; }
  .sample--estate {
    left: 352px; top: 185px; width: 240px; height: 150px;
    background: var(--estate-green); transform: rotate(-11.5deg); transform-origin: 0 0;
  }
  .estate__text {
    position: absolute; left: 16px; top: 14px;
    font-family: var(--sans); font-size: 13px; line-height: 16px; color: var(--estate-yellow);
  }
  .estate__contact {
    position: absolute; left: 16px; top: 70px;
    font-family: var(--sans); font-size: 8px; line-height: 12px; color: var(--estate-yellow);
  }
  .estate__art {
    position: absolute; left: 118px; top: 14px; width: 70px; height: 62px;
    background: linear-gradient(135deg, #a6d468, #8cc63f);
  }

  .sample--dental {
    left: 0; top: 234px; width: 150px; height: 157px; background: var(--dental-blue);
  }
  .dental__photo {
    position: absolute; left: 0; top: 0; width: 150px; height: 102px;
    background: linear-gradient(90deg, #8a5218 0%, #5a3210 55%, #3a220c 100%);
  }
  .dental__smile {
    position: absolute; left: 12px; top: 16px;
    font-family: var(--sans); font-size: 30px; color: var(--ink-white);
  }
  .dental__tagline {
    position: absolute; left: 10px; top: 50px; white-space: nowrap;
    font-family: var(--sans); font-style: italic; font-size: 15px; color: var(--ink-white);
  }
  .dental__name {
    position: absolute; left: 12px; top: 112px;
    font-family: var(--sans); font-weight: 700; font-size: 20px; line-height: 22px; color: var(--ink-white);
  }
  .dental__sub {
    position: absolute; left: 12px; top: 134px;
    font-family: var(--sans); font-size: 13px; line-height: 15px; color: var(--ink-white);
  }
  .dental__note {
    position: absolute; left: 79px; top: 121px; white-space: nowrap;
    font-family: var(--sans); font-size: 8px; line-height: 11px; color: var(--ink-white);
  }

  .sample--auto {
    left: 123px; top: 165px; width: 302px; height: 218px;
    background: var(--ink-white); transform: rotate(11deg); transform-origin: 0 0;
    box-shadow: -2px 3px 6px rgba(0,0,0,.4);
  }
  .auto__brand {
    position: absolute; left: 20px; top: 12px;
    font-family: var(--sans); font-weight: 700; font-size: 41px; line-height: 40px; color: var(--auto-blue);
  }
  .auto__brand-sub {
    position: absolute; left: 22px; top: 52px;
    font-family: var(--sans); font-weight: 700; font-size: 19px; color: var(--auto-grey);
  }
  .auto__lorem {
    position: absolute; left: 22px; top: 96px; width: 112px;
    font-family: var(--sans); font-size: 10.5px; line-height: 12.5px; color: var(--lorem-grey);
  }
  .auto__fine {
    position: absolute; left: 22px; top: 196px;
    font-family: var(--sans); font-size: 5.5px; color: var(--lorem-grey);
  }
  .auto__photo {
    position: absolute; left: 136px; top: 56px; width: 166px; height: 162px;
    background: linear-gradient(160deg, #c7cfc0 0%, #eef0ea 40%, #ffffff 60%, #d9dcde 85%, #9ea3a6 100%);
  }

  .logo { position: absolute; text-align: right; font-family: var(--sans); font-weight: 700; }
  .logo__name { font-size: 21px; line-height: 22px; }
  .logo__tag { font-size: 14px; line-height: 16px; }
  .front__logo { left: 380px; top: 341px; width: 140px; color: var(--ink-white); }

  /* Back */
  .services {
    position: absolute; left: 19px; top: 18px; width: 410px;
    font-family: var(--sans); font-weight: 700; font-style: italic;
    font-size: 32px; line-height: 19.2px; letter-spacing: -0.8px; white-space: nowrap;
    -webkit-mask-image: linear-gradient(90deg, #000 35%, transparent 100%);
            mask-image: linear-gradient(90deg, #000 35%, transparent 100%);
  }
  .services__line { display: block; }
  .services__line--1 { color: #8c8c8c; }
  .services__line--2 { color: #d0d0d0; }
  .services__line--3 { color: #9a9a9a; }
  .services__line--4 { color: #8a8a8a; }
  .services__line--5 { color: #b4b4b4; }
  .services__line--6 { color: #dadada; }
  .services__line--7 { color: #dcdcdc; }

  .stamp-box {
    position: absolute; left: 446px; top: 28px; width: 67px; height: 74px;
    border: 1px solid var(--rule);
  }
  .back__message {
    position: absolute; left: 19px; top: 174px; width: 246px;
    font-family: var(--slab); font-size: 12.6px; line-height: 14px; color: var(--body-ink);
  }
  .specials {
    position: absolute; left: 19px; top: 254px; list-style: none;
    font-family: var(--slab); font-size: 12.6px; line-height: 14px; color: var(--body-ink);
  }
  .specials li::before { content: "» "; }
  .back__visit {
    position: absolute; left: 19px; top: 340px;
    font-family: var(--slab); font-size: 10.5px; color: var(--body-ink);
  }
  .back__visit strong { font-weight: 600; }
  .address-lines { position: absolute; left: 277px; top: 186px; width: 236px; }
  .address-lines span { display: block; height: 1px; background: var(--rule); margin-bottom: 31.5px; }
  .back__logo { left: 390px; top: 328px; width: 121px; color: var(--logo-grey); }
  .back__logo .logo__name { font-size: 15px; line-height: 16px; }
  .back__logo .logo__tag { font-size: 10.5px; line-height: 12px; }
</style>
</head>
<body>
<main class="canvas">

  <section class="postcard postcard--front" aria-label="Postcard front">
    <div class="front__glow" role="img" aria-label="Bright light flare with beams"></div>

    <h1 class="front__headline">Let us make your<br>business shine !</h1>
    <p class="front__order">order 24/7 orders@inkwillow.com</p>

    <div class="sample sample--estate" aria-label="Real estate sample card">
      <p class="estate__text">We are<br>real estate<br>agents</p>
      <p class="estate__contact">12 Elm Street, City<br>info@estatesample.com</p>
      <div class="estate__art" role="img" aria-label="Hand-drawn house illustration"></div>
    </div>

    <div class="sample sample--dental" aria-label="Dentist sample card">
      <div class="dental__photo" role="img" aria-label="Warm toned smile photograph"></div>
      <p class="dental__smile">Smile</p>
      <p class="dental__tagline">with confidence</p>
      <p class="dental__name">ABC</p>
      <p class="dental__sub">dentists</p>
      <p class="dental__note">At vero eos et<br>kasd gubergren, no<br>amet.</p>
    </div>

    <div class="sample sample--auto" aria-label="Auto company sample card">
      <p class="auto__brand">Auto</p>
      <p class="auto__brand-sub">company</p>
      <p class="auto__lorem">Lorem ipsum dolor sit amet, consetetur sadip scing elitr, sed diam nonumy eirmod</p>
      <p class="auto__fine">Lorem ipsum dolor sit amet, consetetur sad</p>
      <div class="auto__photo" role="img" aria-label="Photograph of a white car driving past trees"></div>
    </div>

    <div class="logo front__logo">
      <p class="logo__name">InkWillow</p>
      <p class="logo__tag">logo</p>
    </div>
  </section>

  <section class="postcard postcard--back" aria-label="Postcard back">
    <p class="services" aria-label="Services">
      <span class="services__line services__line--1">business cardsbrochuresbanners</span>
      <span class="services__line services__line--2">calendarscatalogsCD/DVD packages</span>
      <span class="services__line services__line--3">envelopesevent ticketsflyers</span>
      <span class="services__line services__line--4">postcardspresentation folders</span>
      <span class="services__line services__line--5">window cling and decal</span>
      <span class="services__line services__line--6">rack cardslabels</span>
      <span class="services__line services__line--7">table tents</span>
    </p>

    <div class="stamp-box" aria-label="Postage area"></div>

    <p class="back__message">business with no limits, meet mailing with no addresses, gain new customers through “Open Porch Route Drop” reach new customers at their home without needing their address.</p>

    <ul class="specials">
      <li>double your order FREE</li>
      <li>250 100lb gloss stock brochures 99.00</li>
      <li>business packages 299</li>
      <li>1000 flyers 140.40</li>
      <li>5000 postcards 179.99</li>
    </ul>

    <p class="back__visit">visit <strong>inkwillowprint.com</strong> for more info.</p>

    <div class="address-lines" aria-label="Address lines">
      <span></span><span></span><span></span><span></span>
    </div>

    <div class="logo back__logo">
      <p class="logo__name">InkWillow</p>
      <p class="logo__tag">logo</p>
    </div>
  </section>

</main>
</body>
</html>
```